Business Card Design

We like to use greens as you will see in our logo (but not TOO much green). We are a Dental Clinic in a somewhat eccentric community. We do not like the dated sharp designs which we see many dentists use. We're looking for something bright and fresh while still maintaining the integrity of the profession. Elegance is not necessarily what we are going for... we need for the design to be "mature" but also up-lifting.

See our logo.
Updates

Project Deadline Extended
Reason: We have 5 designs which we like. But we'd like to see a few more before committing to a design.

Project Deadline Extended
Reason: We are awaiting revisions to this project. We are still welcoming designs while we wait to see if designers are able to provide to us the revisions we require in order to proceed with a selection.

Target Market(s)

Younger families - ages late 20's to early 40's

Industry/Entity Type

Business

Contact Information for Business Card

Corwel T. Banfry DDS 2730 W. Halvert Rd. Ste. 7 Larkhaven, QZ 48391 (248)555-0174 FX (248)555-0189 info@BrightwellDentalCareMi.com BrigthwellDentalCareMi.com on the back of the card we need an appointment reminder (For____ Date___ Time____) with "If you are unable to keep your appointment, kindly give 48 hours notice" at the bottom. No use of teeth in the design. DOUBLE SIDED DESIGN

Requirements
Should not have
• The use of pictures of teeth

```html
<!DOCTYPE html>
<html lang="en">
<head>
<meta charset="utf-8">
<title>Brightwell Dental Care – Business Card</title>
<link rel="stylesheet" href="https://fonts.googleapis.com/css2?family=Arimo:wght@400;700&family=Crimson+Text:wght@400;600&display=swap">
<style>
  :root {
    --backdrop: #e9e4dc;
    --card: #ffffff;
    --green-dark: #1f6b35;
    --green-light: #8cc63f;
    --ink: #2b2b2b;
    --rule: #8a8a8a;
    --box-line: #6b6b6b;
  }
  * { box-sizing: border-box; margin: 0; padding: 0; }
  html, body { width: 1058px; height: 1200px; overflow: hidden; }
  body {
    background: var(--backdrop);
    font-family: "Arimo", Arial, sans-serif;
    color: var(--ink);
    position: relative;
  }
  .card {
    position: absolute;
    background: var(--card);
    border-radius: 48px;
    box-shadow: 0 4px 14px rgba(0,0,0,.18);
  }
  .card--front { left: 66px; top: 36px; width: 889px; height: 521px; }
  .card--back  { left: 77px; top: 609px; width: 889px; height: 521px; }

  .brand { position: absolute; display: flex; align-items: center; color: var(--green-dark); font-family: "Arimo", Arial, sans-serif; font-weight: 400; }
  .brand__dot { background: var(--green-light); border-radius: 50%; flex: none; }
  .brand__name { line-height: 1.02; }
  .card--front .brand { left: 62px; top: 100px; gap: 20px; }
  .card--front .brand__dot { width: 56px; height: 56px; }
  .card--front .brand__name { font-size: 52px; }
  .card--back .brand { left: 600px; top: 42px; gap: 12px; }
  .card--back .brand__dot { width: 32px; height: 32px; }
  .card--back .brand__name { font-size: 34px; }

  .doctor { position: absolute; left: 44px; top: 300px; font-weight: 700; font-size: 31px; color: var(--green-dark); }
  .website { position: absolute; left: 40px; top: 452px; font-size: 23px; display: flex; align-items: center; gap: 8px; }
  .divider { position: absolute; left: 447px; top: 300px; width: 3px; height: 221px; background: var(--green-light); }
  .contacts { position: absolute; left: 458px; top: 293px; font-size: 23px; line-height: 1; }
  .contacts li { list-style: none; display: flex; align-items: center; gap: 8px; height: 43px; }
  .contacts .address { margin-top: 20px; line-height: 1.27; }
  .icon { width: 18px; height: 18px; fill: var(--green-dark); flex: none; }

  .appt-title { position: absolute; left: 54px; top: 90px; font-family: "Crimson Text", Georgia, serif; font-weight: 600; font-size: 31px; letter-spacing: 1px; color: var(--green-dark); }
  .field { position: absolute; font-size: 23px; }
  .field-line { position: absolute; border-bottom: 2px dotted var(--rule); height: 0; }
  .next-box { position: absolute; left: 326px; top: 295px; width: 488px; height: 33px; border: 2px solid var(--box-line); border-radius: 6px; }
  .day { position: absolute; top: 368px; font-weight: 700; font-size: 24px; color: var(--green-dark); }
  .day-box { position: absolute; top: 364px; width: 54px; height: 33px; border: 2px solid var(--box-line); }
  .separator { position: absolute; left: 0; right: 0; top: 427px; height: 6px; background: linear-gradient(to right, transparent, #d5d5d5 20%, #d5d5d5 80%, transparent); }
  .notice { position: absolute; left: 54px; top: 454px; font-size: 22px; }
</style>
</head>
<body>

<section class="card card--front">
  <div class="brand">
    <span class="brand__dot"></span>
    <span class="brand__name">Brightwell<br>Dental Care</span>
  </div>
  <div class="doctor">Corwel T. Banfry DDS</div>
  <div class="website">
    <svg class="icon" viewBox="0 0 20 20"><circle cx="10" cy="10" r="8.5" fill="none" stroke="#1f6b35" stroke-width="1.8"/><ellipse cx="10" cy="10" rx="3.6" ry="8.5" fill="none" stroke="#1f6b35" stroke-width="1.5"/><path d="M1.5 10h17M3 5.5h14M3 14.5h14" stroke="#1f6b35" stroke-width="1.4"/></svg>
    www.BrigthwellDentalCareMi.com
  </div>
  <div class="divider"></div>
  <ul class="contacts">
    <li><svg class="icon" viewBox="0 0 20 20"><path d="M5 2l3 4-2 2c1 2.5 3.5 5 6 6l2-2 4 3-2 3C9 18 2 11 2 4z"/></svg>(555)555-0174</li>
    <li><svg class="icon" viewBox="0 0 20 20"><rect x="5" y="2" width="10" height="6"/><rect x="1" y="7" width="18" height="8" rx="2"/><rect x="5" y="12" width="10" height="6" fill="#fff" stroke="#1f6b35" stroke-width="1.6"/></svg>(555)555-0189</li>
    <li><svg class="icon" viewBox="0 0 20 20"><rect x="1" y="4" width="18" height="12" rx="1.5"/><path d="M2 5l8 6 8-6" fill="none" stroke="#fff" stroke-width="1.6"/></svg>info@BrightwellDentalCareMi.com</li>
    <li class="address">2730 W. Halvert Rd. Ste. 7<br>Larkhaven, QZ 48391</li>
  </ul>
</section>

<section class="card card--back">
  <h2 class="appt-title">YOUR APPOINTMENT</h2>
  <div class="brand">
    <span class="brand__dot"></span>
    <span class="brand__name">Brightwell<br>Dental Care</span>
  </div>

  <span class="field" style="left:62px;top:177px">Name :</span>
  <span class="field-line" style="left:185px;top:199px;width:626px"></span>

  <span class="field" style="left:62px;top:235px">Date :</span>
  <span class="field-line" style="left:185px;top:257px;width:213px"></span>
  <span class="field" style="left:409px;top:235px">Time :</span>
  <span class="field-line" style="left:485px;top:257px;width:228px"></span>
  <span class="field" style="left:719px;top:235px">am / pm</span>

  <span class="field" style="left:62px;top:298px">Next Appointment</span>
  <span class="next-box"></span>

  <span class="day" style="left:62px">MON</span><span class="day-box" style="left:136px"></span>
  <span class="day" style="left:198px">TUE</span><span class="day-box" style="left:259px"></span>
  <span class="day" style="left:326px">WED</span><span class="day-box" style="left:393px"></span>
  <span class="day" style="left:459px">THU</span><span class="day-box" style="left:523px"></span>
  <span class="day" style="left:586px">FRI</span><span class="day-box" style="left:637px"></span>
  <span class="day" style="left:701px">SAT</span><span class="day-box" style="left:758px"></span>

  <div class="separator"></div>
  <p class="notice">If you are unable to keep your appointment, kindly give 48 hours notice</p>
</section>

</body>
</html>
```